Venture Capital Investment Firm

We are looking to overhaul our existing website (substantially), with only using the same logos (which we can provide).
We are an investment firm that focuses on making loans to late stage technology companies. Our site should ultimately look like other venture capital firms, and look modern and fresh. We have an existing website www.norvellhub.com which this will be replacing, although we will be using a lot of the existing written content, and potentially the numbers of pages we will need, we are not wed to anything else. Please feel free to shoot any questions at any time and thank you in advance for your help!
Websites we like as examples:
https://www.tesmarkfund.com/
https://www.brindlewoodpartners.com/
Target Market(s)
Potential investors who will invest in our firm, as well as potentially companies that are looking to borrow money from us.
Coding
Coded - Design and coding required
Number of Pages Required
5+ page
Colors
Designer to choose colors to be used in the design.
Look and feel

```html
<!DOCTYPE html>
<html lang="en">
<head>
<meta charset="utf-8">
<title>Norvell Hub Investment Partners</title>
<link href="https://fonts.googleapis.com/css2?family=Nunito:wght@400;600;700&family=Montserrat:wght@600;800&display=swap" rel="stylesheet">
<style>
:root{
  --navy:#08073f;
  --navy-deep:#0b0a45;
  --ink:#1e3356;
  --text:#8a8f99;
  --pale:#eef6fd;
  --frame:#d4e9f6;
  --blue-a:#2a69b3;
  --blue-b:#3d9fe2;
  --light-bg:#f7f9fb;
  --white:#ffffff;
}
*{margin:0;padding:0;box-sizing:border-box}
html,body{width:1200px;height:3706px;overflow:hidden}
body{position:relative;font-family:"Nunito",sans-serif;color:var(--ink);background:var(--white)}
.abs{position:absolute}
a{color:inherit;text-decoration:none}

/* header */
.brand{left:80px;top:26px;display:flex;align-items:center;gap:12px}
.brand-mark{width:30px;height:30px;border-radius:50%;background:var(--navy)}
.brand-name{font-size:30px;font-weight:600;color:var(--navy);letter-spacing:.5px;line-height:1}
.brand-sub{font-size:9px;font-weight:700;color:var(--navy);letter-spacing:.5px;margin-top:3px}
.contact-item{display:flex;gap:14px;align-items:flex-start;font-size:13px;color:#55606e;line-height:16px}
.contact-item b{display:block;color:#222;font-weight:700}
.nav{left:80px;top:100px;display:flex;font-size:11px;font-weight:600;color:#333;letter-spacing:.3px}
.nav a{padding:19px 19px 0;height:50px}
.nav a.active{border-top:3px solid var(--ink)}
.nav a:not(:first-child){padding:19px 18px 0}

/* hero */
.hero{left:0;top:150px;width:1200px;height:564px;background:linear-gradient(100deg,#5d6e84 0%,#8696a8 45%,#b9c2cc 70%,#6a7788 100%)}
.hero-overlay{left:0;top:150px;width:1200px;height:344px;background:rgba(40,50,70,.25)}
.hero-kicker{left:80px;top:303px;font:600 13px "Montserrat",sans-serif;letter-spacing:2px;color:#fff}
.hero-title{left:80px;top:324px;font:800 37px/45px "Montserrat",sans-serif;color:#fff;width:640px}
.btn{display:inline-block;background:var(--navy);color:#fff;border-radius:26px;font-size:14px}
.hero-btn{left:80px;top:483px;padding:10px 24px 16px}
.dots{display:flex;gap:11px}
.dot{width:9px;height:9px;border-radius:50%;background:#c9ced6}
.dot.on{background:var(--navy)}

/* services */
.story{left:80px;top:744px;width:409px;height:695px;border:4px solid var(--frame);padding:18px 20px}
.story-photo{width:364px;height:281px;background:linear-gradient(135deg,#d8dde2,#9aa3ac 60%,#5e6770)}
.story h3{font-size:19px;font-weight:700;margin:20px 0 14px;color:var(--ink)}
.story p{font-size:13.5px;line-height:27px;color:var(--text);margin-bottom:14px}
.story .btn{padding:15px 24px;margin-top:4px}
.sec-title{font-size:30px;font-weight:600;color:var(--ink)}
.sec-lede{font-size:13.5px;line-height:27px;color:var(--text)}
.svc{width:284px;height:236px;background:var(--pale);text-align:center;padding:30px 28px 0;clip-path:polygon(0 0,236px 0,284px 48px,284px 100%,0 100%)}
.svc.dark{background:var(--navy);color:#fff}
.svc svg{width:50px;height:50px}
.svc h4{font-size:18px;font-weight:600;color:var(--ink);margin:10px 0 10px}
.svc.dark h4{color:#fff}
.svc p{font-size:13.5px;line-height:27px;color:var(--text)}
.svc.dark p{color:#fff}

/* guidance band */
.band{left:0;width:1200px;background:linear-gradient(90deg,var(--blue-a),var(--blue-b))}
.band-title{font-size:32px;font-weight:600;color:#fff}
.stats{left:80px;top:1624px;width:1040px;height:146px;background:#fff;box-shadow:0 6px 18px rgba(0,0,0,.06);display:flex;padding:38px 28px 0}
.stat{width:253px}
.stat b{display:block;font-size:38px;font-weight:400;color:var(--ink);line-height:1}
.stat i{display:block;width:32px;height:3px;background:var(--ink);margin:10px 0 12px}
.stat span{font-size:13px;font-weight:700;letter-spacing:1.5px;color:#333}

/* blog */
.post{width:327px;border:4px solid var(--frame);background:#fff}
.post-photo{height:256px;position:relative}
.date{position:absolute;left:0;bottom:0;width:44px;height:90px;background:var(--navy);color:#fff;text-align:center;padding-top:10px;font-size:12px;line-height:22px}
.date b{display:block;font-size:20px;font-weight:600}
.post-body{padding:22px 22px 30px}
.post h3{font-size:18.5px;font-weight:400;line-height:28px;color:#222;margin-bottom:18px}
.post p{font-size:13.5px;line-height:27px;color:var(--text);margin-bottom:22px}
.post .btn{padding:7px 12px;font-size:14px}

/* clients */
.clients-bg{left:0;top:2570px;width:1200px;height:610px;background:var(--light-bg)}
.quote-card{width:327px;height:248px;border:4px solid var(--frame);background:var(--light-bg);padding:22px 18px 0 22px;display:flex;gap:20px}
.avatar{width:80px;height:80px;border-radius:50%;background:linear-gradient(135deg,#cfd4da,#6d7680);flex:none}
.quote-card p{font-size:14px;line-height:27px;color:#555}
.quote-card h5{font-size:17px;font-weight:400;color:#222;margin-top:16px}
.quote-card small{font-size:12.5px;color:var(--ink)}
.qmark{width:36px;height:30px}

/* footer */
.footer{left:0;top:3325px;width:1200px;height:381px;background:var(--navy-deep);color:#fff}
.f-head{font-size:18px;font-weight:700}
.f-row{display:flex;gap:20px;font-size:13px;align-items:flex-start;line-height:18px}
.f-links{font-size:13px;line-height:23px;color:#dfe1ee}
.social{display:flex;gap:18px}
.social span{width:32px;height:32px;border-radius:50%;background:#1a195a}
.sub-input{width:240px;height:48px;background:#1b1a57;font-size:14px;text-align:center;line-height:48px;color:#e6e6f0}
.sub-btn{width:240px;height:48px;background:#7f7f86;font-size:14px;text-align:center;line-height:48px}
</style>
</head>
<body>

<!-- header -->
<div class="abs brand">
  <span class="brand-mark"></span>
  <div>
    <div class="brand-name">Norvell Hub</div>
    <div class="brand-sub">INVESTMENT PARTNERS, LLC</div>
  </div>
</div>
<div class="abs contact-item" style="left:600px;top:31px">
  <svg width="18" height="18" viewBox="0 0 24 24"><path d="M2 11 22 2 14 22 11 13Z" fill="#222"/></svg>
  <div><b>Email</b>hello@norvellhub.com</div>
</div>
<div class="abs contact-item" style="left:875px;top:31px">
  <svg width="16" height="16" viewBox="0 0 24 24"><path d="M6.6 10.8a15 15 0 0 0 6.6 6.6l2.2-2.2c.3-.3.7-.4 1-.2 1.1.4 2.3.6 3.6.6.6 0 1 .4 1 1V20c0 .6-.4 1-1 1A17 17 0 0 1 3 4c0-.6.4-1 1-1h3.5c.6 0 1 .4 1 1 0 1.3.2 2.5.6 3.6.1.3 0 .7-.2 1z" fill="#222"/></svg>
  <div><b>Call</b>Call Us: + 1415 7720 46</div>
</div>
<nav class="abs nav">
  <a class="active" href="#">HOME</a><a href="#">STRATEGY</a><a href="#">ABOUT US</a><a href="#">TEAM</a><a href="#">NEWS</a><a href="#">CAREER</a><a href="#">CONTACT</a><a href="#">INVESTORS</a>
</nav>

<!-- hero -->
<div class="abs hero" role="img" aria-label="Business team reviewing documents and a tablet in a bright office"></div>
<div class="abs hero-overlay"></div>
<div class="abs hero-kicker">PARTNERS FOR GROWTH</div>
<h1 class="abs hero-title">WE PROVIDE FLEXIBLE CAPITAL TO INNOVATIVE COMPANIES &amp; THEIR INVESTORS</h1>
<a class="abs btn hero-btn" href="#">Our Services</a>
<div class="abs dots" style="left:586px;top:640px"><span class="dot" style="background:#fff"></span><span class="dot on"></span></div>

<!-- services -->
<div class="abs story">
  <div class="story-photo" role="img" aria-label="Colleagues smiling around a meeting table"></div>
  <h3>Read Our Success Story for Inspiration</h3>
  <p>Far far away, behind the word mountains, far from the countries Vokalia and Consonantia, there live the blind texts. Separated they live in Bookmarksgrove right at the coast of the Semantics, a large language ocean.</p>
  <p>On her way she met a copy. The copy warned the Little Blind Text, that where it came from it would have been rewritten a thousand times and everything that was left from its origin would be the word.</p>
  <a class="btn" href="#">Contact us</a>
</div>
<h2 class="abs sec-title" style="left:525px;top:746px">Our Best Services</h2>
<p class="abs sec-lede" style="left:525px;top:810px;width:595px">On her way she met a copy. The copy warned the Little Blind Text, that where it came from it would have been rewritten a thousand times and everything that was left from its origin would be the word.</p>

<div class="abs svc dark" style="left:525px;top:937px">
  <svg viewBox="0 0 50 50" fill="none" stroke="#fff" stroke-width="1.6"><circle cx="25" cy="10" r="4"/><circle cx="11" cy="30" r="4"/><circle cx="39" cy="30" r="4"/><path d="M19 17h12M13 24l6-8M37 24l-6-8M5 42c0-4 3-6 6-6s6 2 6 6M33 42c0-4 3-6 6-6s6 2 6 6M19 44h12"/></svg>
  <h4>Organization</h4>
  <p>Far far away, behind the word mountains, far from the countries Vokalia.</p>
</div>
<div class="abs svc" style="left:837px;top:937px">
  <svg viewBox="0 0 50 50" fill="none" stroke="#1e3356" stroke-width="1.6"><circle cx="36" cy="10" r="7"/><path d="M36 6v8M33 9l3-3 3 3M4 46h42M8 46V36h5v10M16 46V30h5v16M24 46V26h5v16M32 46V22h5v24M40 46V20h5v26M6 34l12-6 10-4 8-6"/></svg>
  <h4>Marketing Strategy</h4>
  <p>Far far away, behind the word mountains, far from the countries Vokalia.</p>
</div>
<div class="abs svc" style="left:525px;top:1202px">
  <svg viewBox="0 0 50 50" fill="none" stroke="#1e3356" stroke-width="1.6"><circle cx="22" cy="22" r="14"/><circle cx="22" cy="22" r="10"/><path d="M32 32l12 12M14 24l5-5 4 5 5-7M40 6l2 3M44 10l-3 1"/></svg>
  <h4>Risk Analysis</h4>
  <p>Far far away, behind the word mountains, far from the countries Vokalia.</p>
</div>
<div class="abs svc" style="left:837px;top:1202px">
  <svg viewBox="0 0 50 50" fill="none" stroke="#1e3356" stroke-width="1.6"><path d="M25 4v18M25 10c-4-4-8-4-10-2 3 2 6 3 10 2zM25 14c4-4 8-4 10-2-3 2-6 3-10 2zM6 26l10 16 9-8 9 8 10-16M16 30l9 7 9-7"/></svg>
  <h4>Capital Market</h4>
  <p>Far far away, behind the word mountains, far from the countries Vokalia.</p>
</div>

<!-- guidance band with stats -->
<div class="abs band" style="top:1497px;height:173px" role="img" aria-label="Blue-toned photo of people at work"></div>
<h2 class="abs band-title" style="left:0;top:1538px;width:1200px;text-align:center">You Always Get the Best Guidance</h2>
<div class="abs stats">
  <div class="stat"><b>705</b><i></i><span>PROJECTS COMPLETED</span></div>
  <div class="stat"><b>809</b><i></i><span>SATISFIED CUSTOMER</span></div>
  <div class="stat"><b>335</b><i></i><span>AWWARDS RECEIVED</span></div>
  <div class="stat"><b>35</b><i></i><span>YEARS OF EXPERIENCED</span></div>
</div>

<!-- blog -->
<h2 class="abs sec-title" style="left:0;top:1818px;width:1200px;text-align:center">Recent Blog</h2>
<article class="abs post" style="left:80px;top:1938px">
  <div class="post-photo" role="img" aria-label="Hands over charts and a laptop on a desk" style="background:linear-gradient(135deg,#8c949c,#e4e8ec 60%,#c6ccd2)"><div class="date"><b>30</b>April<br>2018</div></div>
  <div class="post-body">
    <h3>Norvell Hub completes structured debt investment in TrailLoom</h3>
    <p>Far far away, behind the word mountains, far from the countries Vokalia and Consonantia, there live the blind texts.</p>
    <a class="btn" href="#">Read More →</a>
  </div>
</article>
<article class="abs post" style="left:436px;top:1938px">
  <div class="post-photo" role="img" aria-label="Three colleagues reviewing a paper together" style="background:linear-gradient(135deg,#e6e1da,#b6a58f 50%,#7a8fae)"><div class="date"><b>06</b>April<br>2016</div></div>
  <div class="post-body">
    <h3>Halvard Microsystems acquired by Crestwave for $55,000,000</h3>
    <p>Far far away, behind the word mountains, far from the countries Vokalia and Consonantia, there live the blind texts.</p>
    <a class="btn" href="#">Read More →</a>
  </div>
</article>
<article class="abs post" style="left:792px;top:1938px">
  <div class="post-photo" role="img" aria-label="Two businessmen in suits at a laptop" style="background:linear-gradient(135deg,#b3bac2,#5d5650 55%,#d8dce0)"><div class="date"><b>19</b>OCT<br>2016</div></div>
  <div class="post-body">
    <h3>Norvell Hub completes $22,000,000 structured debt investment in Pollarity</h3>
    <p>Far far away, behind the word mountains, far from the countries Vokalia and Consonantia, there live the blind texts.</p>
    <a class="btn" href="#">Read More →</a>
  </div>
</article>

<!-- clients -->
<div class="abs clients-bg"></div>
<h2 class="abs sec-title" style="left:0;top:2604px;width:1200px;text-align:center">Our Clients Says</h2>
<p class="abs sec-lede" style="left:280px;top:2670px;width:640px;text-align:center">Separated they live in. A small river named Duden flows by their place and supplies it with the necessary regelialia. It is a paradisematic country</p>

<svg class="abs qmark" style="left:208px;top:2826px" viewBox="0 0 36 30"><path d="M0 30V16C0 7 5 1 15 0v6c-5 1-7 4-7 8h7v16zM21 30V16c0-9 5-15 15-16v6c-5 1-7 4-7 8h7v16z" fill="var(--navy)"/></svg>
<div class="abs quote-card" style="left:80px;top:2845px">
  <div class="avatar" role="img" aria-label="Client portrait"></div>
  <div><p>Far far away, behind the word mountains, far from the countries Vokalia and Consonantia, there live the blind texts.</p><h5>Owen Marsh</h5><small>Businesswoman</small></div>
</div>
<svg class="abs qmark" style="left:564px;top:2826px" viewBox="0 0 36 30"><path d="M0 30V16C0 7 5 1 15 0v6c-5 1-7 4-7 8h7v16zM21 30V16c0-9 5-15 15-16v6c-5 1-7 4-7 8h7v16z" fill="var(--navy)"/></svg>
<div class="abs quote-card" style="left:436px;top:2845px">
  <div class="avatar" role="img" aria-label="Client portrait"></div>
  <div><p>Far far away, behind the word mountains, far from the countries Vokalia and Consonantia, there live the blind texts.</p><h5>Lena Corvi</h5><small>Businesswoman</small></div>
</div>
<svg class="abs qmark" style="left:920px;top:2826px" viewBox="0 0 36 30"><path d="M0 30V16C0 7 5 1 15 0v6c-5 1-7 4-7 8h7v16zM21 30V16c0-9 5-15 15-16v6c-5 1-7 4-7 8h7v16z" fill="var(--navy)"/></svg>
<div class="abs quote-card" style="left:792px;top:2845px">
  <div class="avatar" role="img" aria-label="Client portrait"></div>
  <div><p>Far far away, behind the word mountains, far from the countries Vokalia and Consonantia, there live the blind texts.</p><h5>Tamsin Rowe</h5><small>Businesswoman</small></div>
</div>
<div class="abs dots" style="left:558px;top:3133px;gap:10px"><span class="dot"></span><span class="dot"></span><span class="dot on"></span><span class="dot"></span><span class="dot"></span></div>

<!-- CTA band -->
<div class="abs band" style="top:3180px;height:145px" role="img" aria-label="Blue-toned photo of a business meeting"></div>
<h2 class="abs band-title" style="left:80px;top:3230px">You Always Get the Best Guidance</h2>
<a class="abs" href="#" style="left:881px;top:3226px;width:240px;height:55px;border-radius:28px;background:#fff;color:var(--ink);font-size:14px;text-align:center;line-height:55px">Connect Us</a>

<!-- footer -->
<footer class="abs footer">
  <div class="abs f-head" style="left:80px;top:30px">Reach Us</div>
  <div class="abs f-row" style="left:80px;top:80px;width:320px">
    <svg width="12" height="16" viewBox="0 0 12 16"><path d="M6 0a6 6 0 0 0-6 6c0 4 6 10 6 10s6-6 6-10a6 6 0 0 0-6-6zm0 8.5A2.5 2.5 0 1 1 6 3.5a2.5 2.5 0 0 1 0 5z" fill="#fff"/></svg>
    <span>418 Larkspur Ave. Redwood Park, San Mateo, California, USA</span>
  </div>
  <div class="abs f-row" style="left:80px;top:133px">
    <svg width="14" height="14" viewBox="0 0 24 24"><path d="M6.6 10.8a15 15 0 0 0 6.6 6.6l2.2-2.2c.3-.3.7-.4 1-.2 1.1.4 2.3.6 3.6.6.6 0 1 .4 1 1V20c0 .6-.4 1-1 1A17 17 0 0 1 3 4c0-.6.4-1 1-1h3.5c.6 0 1 .4 1 1 0 1.3.2 2.5.6 3.6.1.3 0 .7-.2 1z" fill="#fff"/></svg>
    <span>+1 650 4418 302</span>
  </div>
  <div class="abs f-row" style="left:80px;top:181px">
    <svg width="16" height="12" viewBox="0 0 16 12"><rect width="16" height="12" rx="1" fill="#fff"/><path d="M0 1l8 6 8-6" stroke="var(--navy-deep)" stroke-width="1.4" fill="none"/></svg>
    <span>info@norvellhub.com</span>
  </div>

  <div class="abs f-head" style="left:458px;top:30px">Links</div>
  <div class="abs f-links" style="left:456px;top:79px">→ Home<br>→ About<br>→ Services<br>→ Projects<br>→ Contact</div>

  <div class="abs f-head" style="left:614px;top:30px">Connect With Us</div>
  <div class="abs social" style="left:616px;top:74px"><span></span><span></span><span></span></div>

  <div class="abs f-head" style="left:881px;top:30px">Subscribe Us!</div>
  <div class="abs sub-input" style="left:881px;top:92px">Enter email address</div>
  <div class="abs sub-btn" style="left:881px;top:148px">Subscribe</div>

  <div class="abs" style="left:0;top:330px;width:1200px;text-align:center;font-size:12.5px">Copyright ©2020 NORVELLHUB All rights reserved</div>
</footer>

</body>
</html>
```